Car transport business

We need a new business card design. Attached is our old card sample. I would just like to adjust the logo colors (blue and red) to be brighter. I changed my name to the brighter red and the word dispatcher to a brighter blue as an example. But you can adjust those colors further. And then perhaps you can use the same colors for the card design but use your imagination.

As a suggestion so the card stands out I would like to add a clip art of car carrier truck. Attached are examples of that as well

```html
<!DOCTYPE html>
<html lang="en">
<head>
<meta charset="utf-8">
<title>Crestline Haul – Business Card</title>
<link rel="stylesheet" href="https://fonts.googleapis.com/css2?family=Montserrat:wght@800&family=Arimo:wght@400;700&display=swap">
<style>
  :root {
    --bg: #c9c9c9;
    --brand-blue: #1f73c8;
    --brand-red: #ec1c24;
    --grad-blue: #1e78c8;
    --grad-purple: #6e4f85;
    --grad-red: #f01a24;
    --ink: #111111;
    --paper: #ffffff;
    --truck-tone: #1a1a1a;
  }
  * { margin: 0; padding: 0; box-sizing: border-box; }
  html, body { width: 1200px; height: 900px; overflow: hidden; }
  body { background: var(--bg); font-family: "Arimo", Arial, sans-serif; position: relative; }

  .card {
    position: absolute;
    border-radius: 26px;
    overflow: hidden;
    box-shadow: 0 10px 22px rgba(0,0,0,0.35);
  }

  /* Front */
  .card--front {
    left: 90px; top: 60px; width: 580px; height: 331px;
    background: linear-gradient(35deg, var(--grad-blue) 0%, var(--grad-purple) 48%, var(--grad-red) 100%);
    display: flex; align-items: center; justify-content: center;
  }
  .brand {
    display: flex; align-items: center; gap: 14px;
    font-family: "Montserrat", Arial, sans-serif; font-weight: 800;
    letter-spacing: 0.02em; text-transform: uppercase;
  }
  .brand__dot { width: 26px; height: 26px; border-radius: 50%; }
  .card--front .brand { color: var(--paper); font-size: 44px; }
  .card--front .brand__dot { background: var(--paper); width: 34px; height: 34px; }

  /* Back */
  .card--back {
    left: 470px; top: 470px; width: 640px; height: 365px;
    background: var(--paper);
  }
  .card--back .brand {
    position: absolute; left: 36px; top: 40px;
    color: var(--brand-blue); font-size: 38px;
  }
  .card--back .brand__dot { background: var(--brand-red); }

  .person { position: absolute; left: 40px; top: 150px; }
  .person__name { font-size: 34px; font-weight: 400; letter-spacing: 0.02em; line-height: 1; }
  .person__first { color: var(--brand-blue); }
  .person__last { color: var(--brand-red); }
  .person__role { color: var(--brand-blue); font-size: 17px; letter-spacing: 0.04em; margin-top: 4px; }

  .contacts { position: absolute; left: 40px; top: 248px; list-style: none; }
  .contacts li {
    display: flex; align-items: center; gap: 10px;
    color: var(--brand-red); font-size: 19px; line-height: 28px;
  }
  .contacts svg { width: 18px; height: 18px; fill: var(--brand-blue); flex: none; }

  .truck-art {
    position: absolute; right: 0; bottom: 60px;
    width: 270px; height: 175px;
    background: linear-gradient(160deg, #3a3a3a, var(--truck-tone));
    border-radius: 8px 0 0 8px;
  }
</style>
</head>
<body>

  <section class="card card--front" aria-label="Card front">
    <div class="brand">
      <span class="brand__dot"></span>
      <span class="brand__name">Crestline Haul</span>
    </div>
  </section>

  <section class="card card--back" aria-label="Card back">
    <div class="brand">
      <span class="brand__dot"></span>
      <span class="brand__name">Crestline Haul</span>
    </div>

    <div class="person">
      <p class="person__name"><span class="person__first">DAN</span> <span class="person__last">MORELL</span></p>
      <p class="person__role">DISPATCHER</p>
    </div>

    <ul class="contacts">
      <li>
        <svg viewBox="0 0 24 24" aria-hidden="true"><path d="M6.6 10.8a15 15 0 0 0 6.6 6.6l2.2-2.2a1 1 0 0 1 1-.25 11.4 11.4 0 0 0 3.6.57 1 1 0 0 1 1 1V20a1 1 0 0 1-1 1A17 17 0 0 1 3 4a1 1 0 0 1 1-1h3.5a1 1 0 0 1 1 1c0 1.25.2 2.45.57 3.6a1 1 0 0 1-.25 1z"/></svg>
        555-201-4830
      </li>
      <li>
        <svg viewBox="0 0 24 24" aria-hidden="true"><path d="M6 2h12v5H6zM4 8h16a2 2 0 0 1 2 2v6h-4v6H6v-6H2v-6a2 2 0 0 1 2-2zm4 8v4h8v-4z"/></svg>
        555-201-4831
      </li>
      <li>
        <svg viewBox="0 0 24 24" aria-hidden="true"><path d="M2 5h20v14H2zm2 2v.5l8 5 8-5V7zm0 2.8V17h16V9.8l-8 5z"/></svg>
        crestlinehaul@example.com
      </li>
    </ul>

    <div class="truck-art" role="img" aria-label="Black clip art of a car carrier truck loaded with cars"></div>
  </section>

</body>
</html>
```